Business Card Design

We provide services doing multiple jobs in the construction industry.Please note: The company name needs to be ROCK SOLID BUILDING SERVICESAttached logo was an example of what we wanted. Can you change up the colors?

Industry/Entity Type

Construction

Contact Information for Business Card

ROCK SOLID BUILDING SERVICES5401 HUDSON BEND RDAUSTIN, TX 78734(512)243-6854ROCKSOLIDBUILDINGSERVICES@GMAIL.COM

```html
<!DOCTYPE html>
<html lang="en">
<head>
<meta charset="utf-8">
<title>Pearlwood Framing Works – Business Card</title>
<link rel="stylesheet" href="https://fonts.googleapis.com/css2?family=Marcellus&family=Open+Sans:wght@400;600&display=swap">
<style>
  :root {
    --backdrop: #ecebe8;
    --navy-deep: #26226e;
    --navy-mid: #3a378f;
    --navy-glow: #4a49a3;
    --ink-navy: #25206b;
    --paper: #ffffff;
    --paper-shade: #f1f1f3;
    --white: #ffffff;
  }
  * { margin: 0; padding: 0; box-sizing: border-box; }
  html, body {
    width: 1200px; height: 858px; overflow: hidden;
    background: var(--backdrop);
  }
  .stage {
    position: relative; width: 1200px; height: 858px;
    display: flex; justify-content: center; align-items: center; gap: 80px;
  }
  .card {
    position: relative; width: 340px; height: 595px;
    box-shadow: 0 14px 34px rgba(0,0,0,.22);
    overflow: hidden;
  }
  .card-front {
    background: radial-gradient(ellipse at 50% 45%, var(--navy-glow) 0%, var(--navy-mid) 45%, var(--navy-deep) 100%);
  }
  .front-name {
    position: absolute; left: 50%; top: 50%;
    transform: translate(-50%, -50%) rotate(-90deg);
    white-space: nowrap;
    font-family: "Open Sans", sans-serif; font-weight: 600;
    font-size: 27px; letter-spacing: 0.5px; color: var(--white);
  }
  .card-back {
    background: linear-gradient(180deg, var(--paper) 0%, var(--paper-shade) 100%);
    display: flex; flex-direction: column; align-items: center;
    padding-top: 120px;
  }
  .brand-mark {
    display: flex; align-items: center; gap: 10px;
    font-family: "Marcellus", serif; font-size: 19px; color: var(--ink-navy);
    letter-spacing: 1px;
  }
  .brand-mark .mark-square { width: 16px; height: 16px; background: var(--ink-navy); }
  .company-name {
    margin-top: 70px; text-align: center; color: var(--ink-navy);
    font-family: "Marcellus", serif;
  }
  .company-name .line-main { display: block; font-size: 34px; letter-spacing: 1px; }
  .company-name .line-sub { display: block; font-size: 22px; letter-spacing: 1px; margin-top: 4px; }
  .contact {
    margin-top: auto; margin-bottom: 90px; text-align: center;
    font-family: "Open Sans", sans-serif; font-size: 13px; line-height: 1.5;
    color: var(--ink-navy);
  }
</style>
</head>
<body>
  <main class="stage">
    <section class="card card-front" aria-label="Card front">
      <p class="front-name">PEARLWOOD FRAMING WORKS</p>
    </section>
    <section class="card card-back" aria-label="Card back">
      <div class="brand-mark">
        <span class="mark-square"></span>
        <span>PEARLWOOD FRAMING WORKS</span>
      </div>
      <h1 class="company-name">
        <span class="line-main">PEARLWOOD</span>
        <span class="line-sub">FRAMING WORKS</span>
      </h1>
      <address class="contact">
        (512)555-0193<br>
        Pearlwoodframingworks@mailnest.example<br>
        7732 Fernglen Pass LN Austin, TX 78734
      </address>
    </section>
  </main>
</body>
</html>
```